Salon and Spa Distributor Business Card

Need a business card. We are are distributor in the salon and spa industry. We identify with natural beauty. Need a card with:
Company Name: Petal Quarry"
Title: "President & CEO"
Address
Company Phone number
email
website
Tag Line:" The Professional Salon Source"

Industry/Entity Type

Business

Contact Information for Business Card

Name: Dov Strommen
Title: "President & CEO"
Address: 31 Harlow Ln, Bexmoor, NJ 07813
Company Phone number: 800-463-5918
email: dovstrommen@petalquarry.example
website: www.petalquarry.example

Requirements
Should not have
• No black backgrounds

```html
<!DOCTYPE html>
<html lang="en">
<head>
<meta charset="utf-8">
<title>Petal Quarry – Business Card</title>
<link rel="stylesheet" href="https://fonts.googleapis.com/css2?family=Questrial&family=Tinos:ital@1&display=swap">
<style>
  :root {
    --leaf-green: #53a641;
    --brand-green: #3f9c35;
    --paper: #f7f7f7;
    --ink: #1e1e1e;
    --white: #ffffff;
    --stage: #ececec;
    --faint-green: rgba(83, 166, 65, 0.12);
  }
  * { box-sizing: border-box; margin: 0; padding: 0; }
  html, body {
    width: 1200px;
    height: 586px;
    overflow: hidden;
  }
  body {
    background: var(--stage);
    position: relative;
    font-family: "Questrial", "Century Gothic", sans-serif;
  }
  .card {
    position: absolute;
    top: 129px;
    width: 501px;
    height: 300px;
    overflow: hidden;
  }

  /* Front */
  .card-front {
    left: 61px;
    background: var(--leaf-green);
    color: var(--white);
  }
  .front-brand {
    position: absolute;
    left: 0;
    right: 0;
    top: 40px;
    display: flex;
    flex-direction: column;
    align-items: center;
    gap: 18px;
  }
  .front-brand .brand-dot {
    width: 110px;
    height: 110px;
    border-radius: 50%;
    background: var(--white);
  }
  .front-brand .brand-name {
    font-size: 30px;
    color: var(--white);
    letter-spacing: 0.02em;
  }
  .front-web {
    position: absolute;
    top: 238px;
    left: 0;
    right: 0;
    display: flex;
    align-items: center;
    justify-content: center;
    gap: 7px;
    font-size: 13px;
    letter-spacing: 0.02em;
  }
  .front-web .rule {
    width: 59px;
    height: 1.5px;
    background: var(--white);
  }
  .tagline {
    position: absolute;
    top: 263px;
    left: 0;
    right: 0;
    text-align: center;
    font-family: "Tinos", "Times New Roman", serif;
    font-style: italic;
    font-size: 12.5px;
    letter-spacing: 0.33em;
  }

  /* Back */
  .card-back {
    left: 619px;
    background: var(--paper);
  }
  .back-decor {
    position: absolute;
    left: 250px;
    top: 110px;
    font-size: 44px;
    color: var(--faint-green);
    white-space: nowrap;
  }
  .back-brand {
    position: absolute;
    left: 28px;
    top: 33px;
    display: flex;
    align-items: center;
    gap: 14px;
  }
  .back-brand .brand-dot {
    width: 60px;
    height: 60px;
    border-radius: 50%;
    background: var(--brand-green);
  }
  .back-brand .brand-name {
    font-size: 24px;
    color: var(--brand-green);
  }
  .person {
    position: absolute;
    left: 29px;
    top: 149px;
  }
  .person-name {
    font-size: 17px;
    color: var(--brand-green);
  }
  .person-title {
    font-family: "Tinos", "Times New Roman", serif;
    font-style: italic;
    font-size: 12px;
    color: var(--ink);
    margin-top: 3px;
  }
  .contacts {
    position: absolute;
    left: 27px;
    top: 211px;
    list-style: none;
  }
  .contacts li {
    display: flex;
    align-items: center;
    gap: 7px;
    height: 24px;
    font-size: 12.5px;
    color: var(--ink);
  }
  .contacts svg {
    width: 17px;
    height: 17px;
    flex: none;
  }
</style>
</head>
<body>

  <section class="card card-front" aria-label="Business card front">
    <div class="front-brand">
      <span class="brand-dot"></span>
      <span class="brand-name">Petal Quarry</span>
    </div>
    <div class="front-web">
      <span class="rule"></span>
      <span>www.petalquarry.example</span>
      <span class="rule"></span>
    </div>
    <p class="tagline">The Professional Salon Source</p>
  </section>

  <section class="card card-back" aria-label="Business card back">
    <div class="back-decor" aria-hidden="true">Petal Quarry</div>

    <div class="back-brand">
      <span class="brand-dot"></span>
      <span class="brand-name">Petal Quarry</span>
    </div>

    <div class="person">
      <p class="person-name">Dov Strommen</p>
      <p class="person-title">President &amp; CEO</p>
    </div>

    <ul class="contacts">
      <li>
        <svg viewBox="0 0 20 20" aria-hidden="true">
          <circle cx="10" cy="10" r="10" fill="var(--brand-green)"/>
          <path d="M5 8.5c0-1.6 2.3-2.6 5-2.6s5 1 5 2.6l-1.8.6-.6-1.4H7.4l-.6 1.4z" fill="#fff"/>
          <rect x="6.5" y="9.5" width="7" height="4.5" rx="1" fill="#fff"/>
        </svg>
        <span>800-463-5918</span>
      </li>
      <li>
        <svg viewBox="0 0 20 20" aria-hidden="true">
          <circle cx="10" cy="10" r="10" fill="var(--brand-green)"/>
          <rect x="5" y="6.5" width="10" height="7" fill="none" stroke="#fff" stroke-width="1.3"/>
          <path d="M5 6.5l5 4 5-4" fill="none" stroke="#fff" stroke-width="1.3"/>
        </svg>
        <span>dovstrommen@petalquarry.example</span>
      </li>
      <li>
        <svg viewBox="0 0 20 20" aria-hidden="true">
          <circle cx="10" cy="10" r="10" fill="var(--brand-green)"/>
          <path d="M10 4a4 4 0 0 0-4 4c0 3 4 7.5 4 7.5s4-4.5 4-7.5a4 4 0 0 0-4-4z" fill="#fff"/>
          <circle cx="10" cy="8" r="1.6" fill="var(--brand-green)"/>
        </svg>
        <span>31 Harlow Ln, Bexmoor, NJ 07813</span>
      </li>
    </ul>
  </section>

</body>
</html>
```